Website for virtual assistant and proofreader

Professional, feminine (but not flowery!) website offering and explaining my services as a VA and Proofreader. Probably only 7 pages: home, about, services (x2), fees, testimonials and contact page. <br/><br/>I already have most of the content, which I have uploaded so you can get an idea of waht I do. I have brand colours and logo already also uploaded. I really just need the bones of the site to be designed and am happy/capable of setting this up as a Wordpress site. I'm just rubbish at design!

Industry/Entity Type

Business Service

Coding

Coded - Design and coding required

Number of Pages Required

4 page

Other font styles liked:
• Roboto Bold + Great Vibes

Colors
3276b5
fee3d4

Requirements
Must have
• should be informative, professional, feminine. Clean, clear, CTA's links to services and fees pages
• Also, see all 3 colour codes on the attached doc.
Nice to have
• business images but place holders will do
Should not have
• Nothing flowery or cartoons! Not 'busy'

```html
<!DOCTYPE html>
<html lang="en">
<head>
<meta charset="utf-8">
<title>Carla M Hayes – Virtual Assistant and Proofreader</title>
<link rel="stylesheet" href="https://fonts.googleapis.com/css2?family=Roboto:wght@400;500;700&family=Great+Vibes&family=Merriweather:wght@300;400&display=swap">
<style>
:root{
  --navy:#0e3d66;
  --navy-deep:#0a355c;
  --peach:#f0bfa8;
  --peach-soft:#fee3d4;
  --taupe:#786d6a;
  --blush:#f4efef;
  --stone:#dcdada;
  --ink:#2b2b2b;
  --white:#ffffff;
  --hero-dark:#15181d;
}
*{box-sizing:border-box;margin:0;padding:0}
html,body{width:1200px;height:5021px;overflow:hidden}
body{position:relative;font-family:"Merriweather",Georgia,serif;color:var(--ink);background:var(--white);font-size:12.5px;line-height:1.55}
.abs{position:absolute}
.heading{font-family:"Roboto",Arial,sans-serif;font-weight:700;text-transform:uppercase;letter-spacing:.5px;color:#1c1c1c}
.rule{display:block;width:58px;height:3px;background:var(--navy);margin-bottom:14px}
.btn{display:inline-block;font-family:"Roboto",Arial,sans-serif;font-weight:700;text-transform:uppercase;font-size:14px;letter-spacing:.5px;text-align:center;text-decoration:none}
.btn-navy{background:var(--navy);color:var(--white)}
.btn-peach{background:var(--peach);color:var(--navy)}
.script{font-family:"Great Vibes",cursive;font-weight:400}

/* header */
.site-header{top:0;left:0;width:1200px;height:87px;background:var(--white);z-index:3}
.logo-disc{left:105px;top:-50px;width:200px;height:190px;border-radius:50%;background:var(--white);z-index:3}
.brand{left:136px;top:60px;z-index:4;display:flex;align-items:center;gap:8px;font-family:"Roboto",Arial,sans-serif;font-weight:500;font-size:15px;color:var(--navy)}
.brand-dot{width:22px;height:22px;border-radius:50%;background:var(--navy)}
.main-nav{left:432px;top:32px;z-index:4;display:flex;gap:18px;font-family:"Roboto",Arial,sans-serif;font-weight:500;font-size:14px;text-transform:uppercase}
.main-nav a{color:#222;text-decoration:none;padding:4px 8px}
.main-nav a.active{background:var(--navy);color:var(--white)}

/* hero */
.hero{top:87px;left:0;width:1200px;height:573px;background:linear-gradient(90deg,#6d7d92 0%,#4b566a 25%,#2a2e36 55%,var(--hero-dark) 75%)}
.hero-title{left:748px;top:200px;font-size:92px;line-height:1.1;color:var(--white);z-index:2}
.hero-sub{left:750px;top:342px;font-family:"Roboto",Arial,sans-serif;font-size:22px;line-height:1.45;color:var(--white);width:300px;z-index:2}
.hero-btn{top:444px;height:48px;line-height:48px;z-index:2}

/* about */
.about-head{left:145px;top:712px;display:flex;align-items:flex-end;gap:22px}
.about-head .heading{font-size:19px}
.about-head .script{font-size:60px;color:var(--navy);line-height:1}
.about-photo{left:145px;top:795px;width:451px;height:525px;background:linear-gradient(160deg,#8b6a4e,#c9a07c 45%,#7a5a3e)}
.about-btn{top:1360px;height:46px;line-height:46px}
.about-copy{left:645px;top:788px;width:424px;font-size:12.5px;line-height:1.53}
.about-copy p{margin-bottom:14px}

/* services */
.services{top:1480px;left:0;width:1200px;height:675px;background:var(--blush)}
.services-intro{left:132px;top:1555px;width:270px}
.services-intro .heading{font-size:20px;margin-bottom:20px}
.services-intro p{font-size:12.5px}
.motto{left:132px;top:1870px;width:320px;border-top:2px solid #c9c3c2;border-bottom:2px solid #c9c3c2;padding:20px 0 30px;font-family:"Roboto",Arial,sans-serif;font-size:31px;line-height:1.45;color:#222}
.service-card{width:248px;height:278px;background:var(--taupe);color:var(--white);text-align:center;padding-top:24px}
.service-card svg{display:block;margin:0 auto 12px}
.service-card h3{font-family:"Roboto",Arial,sans-serif;font-weight:700;font-size:13px;text-transform:uppercase;line-height:1.45;margin-bottom:12px}
.service-card p{font-family:"Roboto",Arial,sans-serif;font-size:11.5px;line-height:1.4;color:#e9e4e2;padding:0 34px;min-height:50px}
.service-card .btn{font-size:10px;width:90px;height:28px;line-height:28px;margin-top:12px}

/* why me */
.why{top:2155px;left:0;width:1200px;height:393px;background:radial-gradient(ellipse at 20% 30%,#fbeee8 0,transparent 30%),radial-gradient(ellipse at 85% 70%,#fbeee8 0,transparent 30%),var(--white)}
.why-quill{left:565px;top:2200px;width:72px;height:130px;background:linear-gradient(180deg,#c7917d,#2c5d9a);border-radius:36px 36px 10px 10px}
.why-title{left:0;top:2368px;width:1200px;text-align:center;font-size:19px}
.why-copy{left:330px;top:2412px;width:540px;text-align:center;font-size:12.5px}

/* help columns */
.help-left{top:2548px;left:0;width:584px;height:527px;background:var(--stone)}
.help-right{top:2548px;left:584px;width:616px;height:527px;background:var(--navy-deep)}
.col-copy{width:340px;font-size:12.5px}
.col-copy .heading{font-size:20px;margin-bottom:24px;line-height:1.3}
.col-copy p{margin-bottom:18px}
.help-right .col-copy,.help-right .col-copy .heading{color:#dce5ef}
.help-right .rule{background:var(--white)}

/* story */
.story{top:3075px;left:0;width:1200px;height:1235px;background:var(--blush)}
.story-title{left:138px;top:3140px;font-size:20px}
.story-copy{left:138px;top:3220px;width:534px;font-size:12.5px;text-align:justify;line-height:1.53}
.story-copy p{margin-bottom:18px}
.story-feather{left:760px;top:3250px;width:260px;height:760px;border-radius:50% 50% 40% 40%/60% 60% 30% 30%;background:linear-gradient(160deg,#f6d5c6,#eeb79e);transform:rotate(14deg);opacity:.8}
.certs{left:135px;top:4090px;width:933px;height:170px;background:var(--taupe);color:var(--white)}
.certs h3{position:absolute;left:40px;top:56px;width:250px;text-align:center;font-family:"Roboto",Arial,sans-serif;font-weight:700;font-size:17px;line-height:1.5;text-transform:uppercase}
.certs .divider{position:absolute;left:290px;top:24px;width:2px;height:122px;background:var(--white)}
.certs .lead{position:absolute;left:337px;top:24px;font-family:"Roboto",Arial,sans-serif;font-size:14px;color:#ece6e4}
.certs ul{position:absolute;top:66px;list-style:none;font-family:"Roboto",Arial,sans-serif;font-weight:500;font-size:12.5px;line-height:1.45}

/* testimonials */
.testimonials-title{left:0;top:4350px;width:1200px;text-align:center}
.testimonials-title .rule{margin:0 auto 26px;width:42px}
.testimonials-title .heading{font-size:19px}
.testimonial{top:4446px;width:297px;height:279px;background:var(--white);border:1px solid #cfcfcf;padding:32px 30px 0 32px;font-family:"Roboto",Arial,sans-serif;font-size:11.5px;line-height:1.5;color:#333}
.testimonial .q{font-size:30px;font-weight:700;color:var(--navy);line-height:.6;display:block;margin-bottom:10px}
.testimonial .qe{font-size:30px;font-weight:700;color:var(--navy);position:absolute;right:120px;top:205px}
.testimonial cite{position:absolute;left:32px;top:228px;font-style:normal;font-weight:700;color:var(--navy);font-size:12px}
.arrow{top:4568px}

/* footer */
.site-footer{top:4846px;left:0;width:1200px;height:175px;background:var(--blush)}
.footer-logo-art{left:128px;top:4790px;width:78px;height:200px;background:linear-gradient(180deg,#c7917d,#2c5d9a);border-radius:39px 39px 12px 12px}
.footer-brand{left:215px;top:4915px;font-family:"Roboto",Arial,sans-serif;font-weight:500;font-size:28px;line-height:1.2;color:var(--navy)}
.footer-tag{left:218px;top:4955px;font-family:"Roboto",Arial,sans-serif;font-size:15px;color:var(--navy)}
.follow{left:928px;top:4888px;display:flex;align-items:center;gap:6px;font-family:"Roboto",Arial,sans-serif;font-size:10px;text-transform:uppercase}
.follow span.dot{width:22px;height:22px;border-radius:50%;background:var(--navy)}
.footer-nav{left:538px;top:4954px;display:flex;gap:22px;font-family:"Roboto",Arial,sans-serif;font-size:13px;font-weight:500;text-transform:uppercase}
.footer-nav a{color:#222;text-decoration:none}
.copyright{left:866px;top:4986px;font-family:"Roboto",Arial,sans-serif;font-size:10px;color:#333}
</style>
</head>
<body>

<!-- header -->
<header class="site-header abs"></header>
<div class="logo-disc abs"></div>
<div class="brand abs"><span class="brand-dot"></span>Carla M Hayes</div>
<nav class="main-nav abs">
  <a class="active" href="#">Home</a><a href="#">Services</a><a href="#">System Applications</a><a href="#">Fees</a><a href="#">Why Me?</a><a href="#">Contact</a>
</nav>

<!-- hero -->
<section class="hero abs" role="img" aria-label="Hands working on a laptop and writing notes with a pencil"></section>
<h1 class="hero-title abs script">Allow me...</h1>
<p class="hero-sub abs">to handle the details so you can get on with business.</p>
<a class="btn btn-navy hero-btn abs" style="left:751px;width:196px" href="#">Learn More</a>
<a class="btn btn-peach hero-btn abs" style="left:962px;width:146px" href="#">Contact</a>

<!-- about -->
<section class="about">
  <div class="about-head abs">
    <div><span class="rule"></span><h2 class="heading">About Me</h2></div>
    <span class="script">Carla M Hayes</span>
  </div>
  <div class="about-photo abs" role="img" aria-label="Portrait photograph of the virtual assistant"></div>
  <a class="btn btn-navy about-btn abs" style="left:209px;width:143px" href="#">Learn More</a>
  <a class="btn btn-peach about-btn abs" style="left:372px;width:143px" href="#">Contact</a>
  <div class="about-copy abs">
    <p>Every great leader is backed by diligent and knowledgeable support. Have you ever wondered what it would be like to have your very own personal assistant? Well, you can. A virtual assistant can do everything a full-time assistant can, with the added bonus that she can save you money. Whether you need daily help, or help with special assignments or big projects, hiring me as your VA will save you the costs typically associated with an employee--holiday pay, sick pay, overtime, taxes, and insurance, are no longer your concern. And, as a virtual assistant, I only charge for the hours I actually work--no more resource-siphoning downtime.</p>
    <p>Allow me to be of service. Answering emails, organizing client files, managing projects, updating website content, proofreading content, they are all important tasks but not so important that you have to do them yourself. I have rescued many businesses from the throws of chaos, bringing order to a seemingly endless onslaught of details and procedures. I can make your business function optimally. And as an independent agent, I can do it for a fraction of the cost of a full-time right-hand assistant.</p>
    <p>From organizing existing businesses to creating systems and procedures to launching a fledgling business, I offer decades of experience mastering the minutiae so your business can function at its optimum.</p>
    <p>So trust your important tasks to a professional specially qualified to handle the mundane and minutiae. Delegate to an expert and restore the life-work balance that will benefit you, your clients, and your personal relationships.</p>
    <p>Isn't it time you hire the right-hand support your business needs and you deserve?</p>
  </div>
</section>

<!-- services -->
<section class="services abs"></section>
<div class="services-intro abs">
  <span class="rule"></span>
  <h2 class="heading">Our Services</h2>
  <p>Do you need some Smart Office Support (SOS)? Do you have a huge project looming on the horizon? Do you just need a little support managing the growing stacks of To-Dos cluttering your desk? As a master of managing the barrage of daily details that require concise and prompt attention, SOS is my speciality, from organisation to proofreading, no detail is too small!</p>
</div>
<p class="motto abs">If you want something done right... find the right person to do it!</p>

<div class="service-card abs" style="left:547px;top:1533px">
  <svg width="60" height="60" viewBox="0 0 60 60" fill="none" stroke="#fff" stroke-width="2"><rect x="12" y="10" width="30" height="40" rx="2"/><rect x="20" y="6" width="14" height="8" rx="2"/><path d="M18 22h18M18 30h12M18 38h8"/><circle cx="44" cy="44" r="9"/><path d="M44 39v5l3 3"/></svg>
  <h3>Organizational/<br>Project Management</h3>
  <p>Reliable project and team management, master of organisation</p>
  <a class="btn btn-peach" href="#">Learn More</a>
</div>
<div class="service-card abs" style="left:810px;top:1533px">
  <svg width="60" height="60" viewBox="0 0 60 60" fill="none" stroke="#fff" stroke-width="2"><path d="M14 34v-6a16 16 0 0 1 32 0v6"/><rect x="10" y="32" width="8" height="14" rx="3"/><rect x="42" y="32" width="8" height="14" rx="3"/><path d="M46 46c0 6-6 8-12 8"/></svg>
  <h3>Administrative and<br>Accounting Support:</h3>
  <p>Work smarter not harder with the right VA by your side</p>
  <a class="btn btn-peach" href="#">Learn More</a>
</div>
<div class="service-card abs" style="left:547px;top:1825px">
  <svg width="60" height="60" viewBox="0 0 60 60" fill="none" stroke="#fff" stroke-width="2"><rect x="8" y="10" width="44" height="34" rx="2"/><path d="M8 18h44M14 26h14M14 32h10"/><circle cx="40" cy="34" r="7"/><circle cx="40" cy="34" r="2"/><path d="M24 52h12M30 44v8"/></svg>
  <h3>Website<br>Administration</h3>
  <p>Dependable and reliable website updates--like clockwork</p>
  <a class="btn btn-peach" href="#">Learn More</a>
</div>
<div class="service-card abs" style="left:810px;top:1825px">
  <svg width="60" height="60" viewBox="0 0 60 60" fill="none" stroke="#fff" stroke-width="2"><path d="M14 6h22l10 10v38H14z"/><path d="M36 6v10h10M20 24h18M20 30h14M20 36h10"/><circle cx="40" cy="44" r="8"/><path d="M37 47l6-6"/></svg>
  <h3>Editorial Service<br>/Proofreading</h3>
  <p>Catching simple typos and grammatical faux pas to preserve your integrity</p>
  <a class="btn btn-peach" href="#">Learn More</a>
</div>

<!-- why me -->
<section class="why abs" role="img" aria-label="Soft scattered peach feathers on a white background"></section>
<div class="why-quill abs" role="img" aria-label="Quill pen resting in an ink pot"></div>
<h2 class="why-title heading abs">Why Me?</h2>
<p class="why-copy abs">I offer administrative, management, and editorial services for those in need of an expert, professional, and discreet "virtual" assistant. As an independent contractor, I can offer you these services with all the same dedication and loyalty as a full-time staff assistant -- at a more cost-effective rate</p>

<!-- who benefited / what I can do -->
<section class="help-left abs">
  <div class="col-copy abs" style="left:132px;top:52px">
    <span class="rule"></span>
    <h2 class="heading">Who's Benefited<br>From My Help..</h2>
    <p>My employers and clients hail from backgrounds in marketing, education, import/export businesses, IT, health and wellbeing and hospitality. They range from small to large businesses and individuals, all with a common issue -- they needed help managing the day-to-day details that make their operations run smoothly.</p>
    <p>My clients are entrepreneurs, consultants, charitable organisations, small businesses, students and professors -- all of whom can attest to the benefits of outsourcing time-consuming tasks that distract them from their primary mission.</p>
  </div>
</section>
<section class="help-right abs">
  <div class="col-copy abs" style="left:83px;top:52px;width:360px">
    <span class="rule"></span>
    <h2 class="heading">What I Can Do For You...</h2>
    <p>Sales accounting, inventory control, social media management, general office support, marketing assistance, client or HR relations, project management, contract reviews, regulatory compliance documentation ... essentially any area of business that can benefit from administrative support, you'll find I can deliver exemplary service. There is no job too big or too small.</p>
    <p>And, as of 2019, I am proud to announce that I am expanding my services to offer editorial services after completing my Professional Certificate for Proofreading. I look forward to offering this service to business and individuals who prepare proposals, investor reports, academic papers, grant writers, and even blog posts and web pages. Let me put the perfect polish on your public prose.</p>
  </div>
</section>

<!-- story -->
<section class="story abs"></section>
<span class="rule abs" style="left:138px;top:3118px;width:42px"></span>
<h2 class="story-title heading abs">Sometimes your calling... well, it finds you!</h2>
<div class="story-copy abs">
  <p>I have over 30-years experience rescuing countless businesses from backlogs of work or faulty practices, and I have helped launched almost as many new businesses by building a solid foundation on sound systems. I have a history of arriving in just the right place at just the right time -- when businesses and professionals need me the most.</p>
  <p>I have fine-tuned my administration skills and operational and organisational insights over three decades, starting in a local government office in the UK. Over the course of those years, I have amassed experience in accounting, stock purchasing and management, IT support (research, purchase, installation, and maintenance of software), personnel training and management, general PA duties, business compliance (insurance, fire, health &amp; safety regulations), contract management, and human resources services -- skills built on a strong foundation of office and administrative expertise.</p>
  <p>After many years in the corporate world as a customer service representative, I landed in the import/export business, coordinating stock production with China (in association with the APAC Operations Director) for distribution throughout the UK, Europe, South Africa, South America, and the USA. Under the Managing Director, I prepared weekly, monthly, and quarterly financial reports for distribution to stakeholders as well as staff. I managed a team effort to plan, coordinate and provide seminars, exhibitions, marketing campaigns, and product launches.</p>
  <p>Before embarking on my own, I was the go-to gal for Speak Easy Languages, a language school in Thailand, instituting new software systems and procedures to streamline and expedite the management of student records and government compliances documentation (Visas). I managed the school's website development and daily administration, directed email marketing campaigns and liaised with the public, students and businesses, providing a unified image to our community, our target market.</p>
  <p>I am conscientious, meticulous, methodical, diligent and driven. I am a strategic thinker, skilled at organisation and plan execution. I love a challenge and am continually learning new applications and platforms to help me deliver on my promises to you.</p>
  <p>With my help, you never have to wonder if your project will be completed on time or to your standards. I have a very hands-on approach involvement with my clients, their projects and their businesses.</p>
  <p>Allow me to assist you and restore your work-life balance.</p>
</div>
<div class="story-feather abs" role="img" aria-label="Large peach feather illustration"></div>

<div class="certs abs">
  <h3>Certifications<br>and Qualifications</h3>
  <span class="divider"></span>
  <span class="lead">Professional Certificate for Proofreading</span>
  <ul style="left:337px">
    <li>Diploma for Documents and Spreadsheets</li>
    <li>Thai language – A1</li>
    <li>Spanish to GCSE Level – A1</li>
    <li>NBK Book-keeping Stage 1</li>
  </ul>
  <ul style="left:614px">
    <li>Qualified TEFL teacher</li>
    <li>Trade Guild Board in Public House Management</li>
    <li>6 C.S.E. Grade 3 and above, 2 'O' Levels</li>
    <li>Many other online courses</li>
  </ul>
</div>

<!-- testimonials -->
<div class="testimonials-title abs">
  <span class="rule"></span>
  <h2 class="heading">Testimonials</h2>
</div>
<svg class="arrow abs" style="left:80px" width="14" height="24" viewBox="0 0 14 24" fill="none" stroke="#555" stroke-width="2"><path d="M12 2L2 12l10 10"/></svg>
<svg class="arrow abs" style="left:1104px" width="14" height="24" viewBox="0 0 14 24" fill="none" stroke="#555" stroke-width="2"><path d="M2 2l10 10L2 22"/></svg>
<blockquote class="testimonial abs" style="left:130px"><span class="q">“</span>Lorem ipsum dolor sit amet, conse ctetur adipiscing elit, sed do eiusmod tempor incididunt ut labore et dolore magna aliqua. Ut enim ad minim ven iam, quis nostrud exercitation ullamco laboris nisi ut aliquip ex ea commodo consequat. Duis aute irure dolor in reprehenderit in voluptate velit esse cillum dolore eu fugiat.<span class="qe">”</span><cite>RICHARD</cite></blockquote>
<blockquote class="testimonial abs" style="left:451px"><span class="q">“</span>Lorem ipsum dolor sit amet, conse ctetur adipiscing elit, sed do eiusmod tempor incididunt ut labore et dolore magna aliqua. Ut enim ad minim ven iam, quis nostrud exercitation ullamco laboris nisi ut aliquip ex ea commodo consequat. Duis aute irure dolor in reprehenderit in voluptate velit esse cillum dolore eu fugiat.<span class="qe">”</span><cite>RICHARD</cite></blockquote>
<blockquote class="testimonial abs" style="left:772px"><span class="q">“</span>Lorem ipsum dolor sit amet, conse ctetur adipiscing elit, sed do eiusmod tempor incididunt ut labore et dolore magna aliqua. Ut enim ad minim ven iam, quis nostrud exercitation ullamco laboris nisi ut aliquip ex ea commodo consequat. Duis aute irure dolor in reprehenderit in voluptate velit esse cillum dolore eu fugiat.<span class="qe">”</span><cite>RICHARD</cite></blockquote>

<!-- footer -->
<footer class="site-footer abs"></footer>
<div class="footer-logo-art abs" role="img" aria-label="Quill pen in an ink pot"></div>
<div class="footer-brand abs">Carla M Hayes</div>
<div class="footer-tag abs">Virtual Assistant and Proofreader</div>
<div class="follow abs">Follow <span class="dot"></span><span class="dot"></span><span class="dot"></span></div>
<nav class="footer-nav abs">
  <a href="#">Home</a><a href="#">Services</a><a href="#">System Applications</a><a href="#">Fees</a><a href="#">Why Me?</a><a href="#">Contact</a>
</nav>
<p class="copyright abs">Copyright © 2020 All Rights Reserved</p>

</body>
</html>
```